Banner ad series

We need a series of banner ads for 4 different digital products. The ads will drive traffic to these landing pages:
Relocate.set: http://pinnedtidygoods.example/relocatekit/
Treasures.file: http://pinnedtidygoods.example/digital-treasures-file/
Jumpstart Drill School: http://pinnedtidygoods.example/jumpstart-drill-school/
Vital Habits Drill School: http://pinnedtidygoods.example/vital-habits/

Banner Ad Sizes needed:
160x600, 728x90, 300x250

Text files with the copy/variations needed for each product are attached. In the text file - the first line of each option is the main headline. All other copy is support copy and OPTIONAL.

Target Market(s)

Our target market is a woman between the ages of 30-55 with kids. She's smart, working professionally and always on the lookout for products and services that will help her get more organized.

Industry/Entity Type

Digital

Requirements
Must have
• Pinned Tidy logo

```html
<!DOCTYPE html>
<html lang="en">
<head>
<meta charset="utf-8">
<title>Pinned Tidy – Jumpstart Drill School banner set</title>
<link rel="stylesheet" href="https://fonts.googleapis.com/css2?family=Open+Sans:wght@400;600;700&display=swap">
<style>
  :root {
    --bg: #e9e6e1;
    --green: #2f9a14;
    --green-light: #7ac943;
    --yellow: #ffd200;
    --white: #ffffff;
    --ink: #222222;
    --brand: #d2186b;
    --orange-top: #ffa040;
    --orange-bottom: #e85f00;
    --photo-a: #f4f2ee;
    --photo-b: #d9dcd6;
    --rule: rgba(255,255,255,0.45);
  }
  * { box-sizing: border-box; margin: 0; padding: 0; }
  html, body { width: 1200px; height: 800px; overflow: hidden; }
  body {
    background: var(--bg);
    font-family: "Open Sans", Arial, sans-serif;
    position: relative;
  }
  .banner {
    position: absolute;
    overflow: hidden;
    background: var(--white);
    box-shadow: 0 4px 12px rgba(0,0,0,0.25);
  }
  .banner svg.shape { position: absolute; inset: 0; width: 100%; height: 100%; }
  .photo {
    position: absolute;
    background: linear-gradient(160deg, var(--photo-a), var(--photo-b));
  }
  .logo {
    position: absolute;
    display: flex;
    align-items: center;
    gap: 8px;
    background: var(--white);
    padding: 0 12px;
  }
  .logo-dot { width: 14px; height: 14px; border-radius: 50%; background: var(--brand); flex: none; }
  .logo-name { color: var(--brand); font-weight: 700; font-size: 17px; white-space: nowrap; }
  .copy { position: absolute; color: var(--white); text-align: center; }
  .headline { font-weight: 700; text-transform: uppercase; line-height: 1.15; }
  .headline .accent { color: var(--yellow); }
  .subhead { font-weight: 700; text-transform: uppercase; line-height: 1.2; }
  .support { font-weight: 400; line-height: 1.25; }
  .rule { border: 0; border-top: 1px dotted var(--rule); }
  .cta {
    position: absolute;
    display: flex;
    align-items: center;
    justify-content: center;
    gap: 8px;
    color: var(--white);
    font-weight: 700;
    border-radius: 999px;
    background: linear-gradient(var(--orange-top), var(--orange-bottom));
    border: 2px solid #ffd7ad;
    box-shadow: 0 2px 4px rgba(0,0,0,0.35);
    white-space: nowrap;
  }
  .cta-arrow { width: 26px; height: 26px; flex: none; }

  /* 160x600 skyscraper */
  .skyscraper { left: 89px; top: 71px; width: 183px; height: 683px; }
  .skyscraper .logo { left: 10px; top: 12px; width: 163px; height: 62px; justify-content: center; border: 1px solid #ddd; }
  .skyscraper .photo { left: 0; top: 87px; width: 183px; height: 270px; }
  .skyscraper .copy { left: 6px; width: 171px; top: 375px; }
  .skyscraper .headline { font-size: 22px; }
  .skyscraper .rule { margin: 12px 8px; }
  .skyscraper .subhead { font-size: 19px; }
  .skyscraper .support { font-size: 14.5px; }
  .skyscraper .cta { left: 8px; top: 628px; width: 167px; height: 40px; font-size: 17px; }

  /* 300x250 rectangle */
  .rectangle { top: 261px; width: 343px; height: 283px; }
  .rectangle.first { left: 341px; }
  .rectangle.second { left: 697px; }
  .rectangle .photo { left: 150px; top: 0; width: 193px; height: 283px; }
  .rectangle .logo { left: 8px; top: 7px; width: 158px; height: 50px; justify-content: center; border: 1px solid #ddd; }
  .rectangle .copy { left: 4px; width: 172px; top: 90px; }
  .rectangle .headline { font-size: 20px; }
  .rectangle .subhead { font-size: 18px; margin-top: 10px; }
  .rectangle .rule { margin: 6px 10px; }
  .rectangle .support { font-size: 13.5px; }
  .rectangle .cta { left: 172px; top: 233px; width: 160px; height: 38px; font-size: 16px; }

  /* 728x90 leaderboard */
  .leaderboard { left: 287px; top: 569px; width: 832px; height: 102px; }
  .leaderboard .photo { left: 560px; top: 0; width: 272px; height: 102px; }
  .leaderboard .logo { left: 8px; top: 18px; width: 159px; height: 66px; justify-content: center; border: 1px solid #ddd; }
  .leaderboard .copy { left: 180px; width: 400px; top: 8px; }
  .leaderboard .headline { font-size: 22px; line-height: 1.1; }
  .leaderboard .support { font-size: 14px; margin-top: 2px; }
  .leaderboard .cta { left: 635px; top: 30px; width: 162px; height: 40px; font-size: 16px; }
</style>
</head>
<body>

<!-- Skyscraper 160x600 -->
<section class="banner skyscraper" aria-label="Skyscraper banner">
  <div class="photo" role="img" aria-label="Photo of a tidy white wall organizer with files, notes and hooks"></div>
  <svg class="shape" viewBox="0 0 183 683" preserveAspectRatio="none" aria-hidden="true">
    <path d="M0 360 Q90 330 183 318 V683 H0 Z" fill="var(--green)"/>
    <path d="M0 360 Q90 330 183 318" fill="none" stroke="var(--green-light)" stroke-width="4"/>
  </svg>
  <div class="logo"><span class="logo-dot"></span><span class="logo-name">Pinned Tidy</span></div>
  <div class="copy">
    <p class="headline">Now that it's<br><span class="accent">the new year</span></p>
    <hr class="rule">
    <p class="subhead">It's time to<br>get organized!</p>
    <hr class="rule">
    <p class="support">Sign Up for the Jumpstart Drill School &amp; Organize your home AND your life</p>
  </div>
  <div class="cta">Learn More!
    <svg class="cta-arrow" viewBox="0 0 26 26" aria-hidden="true"><circle cx="13" cy="13" r="12" fill="#222"/><path d="M10 7 L16 13 L10 19" fill="none" stroke="#fff" stroke-width="3"/></svg>
  </div>
</section>

<!-- Rectangle 300x250 -->
<section class="banner rectangle first" aria-label="Rectangle banner">
  <div class="photo" role="img" aria-label="Photo of a tidy white wall organizer with files and notes"></div>
  <svg class="shape" viewBox="0 0 343 283" preserveAspectRatio="none" aria-hidden="true">
    <path d="M0 62 H200 Q220 20 248 0 H252 Q185 90 182 283 H0 Z" fill="var(--green)"/>
    <path d="M252 0 Q185 90 182 283" fill="none" stroke="var(--green-light)" stroke-width="4"/>
    <rect x="0" y="0" width="200" height="62" fill="var(--white)"/>
  </svg>
  <div class="logo"><span class="logo-dot"></span><span class="logo-name">Pinned Tidy</span></div>
  <div class="copy">
    <p class="headline">Now that it's<br><span class="accent">the new year</span></p>
    <p class="subhead">It's time to<br>get organized!</p>
    <hr class="rule">
    <p class="support">Sign Up for the Jumpstart Drill School &amp; Organize your home AND your life</p>
  </div>
  <div class="cta">Learn More!
    <svg class="cta-arrow" viewBox="0 0 26 26" aria-hidden="true"><circle cx="13" cy="13" r="12" fill="#222"/><path d="M10 7 L16 13 L10 19" fill="none" stroke="#fff" stroke-width="3"/></svg>
  </div>
</section>

<section class="banner rectangle second" aria-label="Rectangle banner">
  <div class="photo" role="img" aria-label="Photo of a tidy white wall organizer with files and notes"></div>
  <svg class="shape" viewBox="0 0 343 283" preserveAspectRatio="none" aria-hidden="true">
    <path d="M0 62 H200 Q220 20 248 0 H252 Q185 90 182 283 H0 Z" fill="var(--green)"/>
    <path d="M252 0 Q185 90 182 283" fill="none" stroke="var(--green-light)" stroke-width="4"/>
    <rect x="0" y="0" width="200" height="62" fill="var(--white)"/>
  </svg>
  <div class="logo"><span class="logo-dot"></span><span class="logo-name">Pinned Tidy</span></div>
  <div class="copy">
    <p class="headline">Now that it's<br><span class="accent">the new year</span></p>
    <p class="subhead">It's time to<br>get organized!</p>
    <hr class="rule">
    <p class="support">Sign Up for the Jumpstart Drill School &amp; Organize your home AND your life</p>
  </div>
  <div class="cta">Learn More!
    <svg class="cta-arrow" viewBox="0 0 26 26" aria-hidden="true"><circle cx="13" cy="13" r="12" fill="#222"/><path d="M10 7 L16 13 L10 19" fill="none" stroke="#fff" stroke-width="3"/></svg>
  </div>
</section>

<!-- Leaderboard 728x90 -->
<section class="banner leaderboard" aria-label="Leaderboard banner">
  <div class="photo" role="img" aria-label="Photo of white wall organizer shelves with files"></div>
  <svg class="shape" viewBox="0 0 832 102" preserveAspectRatio="none" aria-hidden="true">
    <path d="M175 0 H600 Q560 50 555 102 H175 Z" fill="var(--green)"/>
    <path d="M600 0 Q560 50 555 102" fill="none" stroke="var(--green-light)" stroke-width="4"/>
  </svg>
  <div class="logo"><span class="logo-dot"></span><span class="logo-name">Pinned Tidy</span></div>
  <div class="copy">
    <p class="headline">Now that it's <span class="accent">the new year</span><br>It's time to get organized!</p>
    <p class="support">Sign Up for the Jumpstart Drill School &amp; Organize your home AND your life</p>
  </div>
  <div class="cta">Learn More!
    <svg class="cta-arrow" viewBox="0 0 26 26" aria-hidden="true"><circle cx="13" cy="13" r="12" fill="#222"/><path d="M10 7 L16 13 L10 19" fill="none" stroke="#fff" stroke-width="3"/></svg>
  </div>
</section>

</body>
</html>
```